Local fast-growing company in the service sector

We are looking for a modern business card design, which should also appear on our letterheads

Target Market(s)

Private and industrial sectors

Contact Information for Business Card

Vorname Name
Kellberger Str. 18
72486 Brunnstadt
Tel.: 07146-839214-0
Name@agentur-kvtl.de

Colors
9d9d9d
919191
aaaaaa

Requirements
Must have
• The logo (file) in silver

```html
<!DOCTYPE html>
<html lang="de">
<head>
<meta charset="utf-8">
<title>KVTL Visitenkarte</title>
<link href="https://fonts.googleapis.com/css2?family=Open+Sans:wght@400;600;700&display=swap" rel="stylesheet">
<style>
  :root {
    --stage: #e6e6e6;
    --silver-light: #c4c4c4;
    --silver: #aaaaaa;
    --silver-mid: #9d9d9d;
    --silver-dark: #919191;
    --paper: #ffffff;
    --ink: #4a4a4a;
    --ink-dark: #1e1e1e;
    --tag: #bdbdbd;
  }
  * { box-sizing: border-box; margin: 0; padding: 0; }
  html, body { width: 1200px; height: 900px; overflow: hidden; }
  body {
    background: var(--stage);
    font-family: "Open Sans", sans-serif;
    position: relative;
  }
  .card {
    position: absolute;
    left: 267px;
    width: 666px;
    height: 380px;
    overflow: hidden;
    box-shadow: 0 6px 18px rgba(0,0,0,.18);
  }
  .card--front {
    top: 50px;
    background: radial-gradient(ellipse at 55% 35%, var(--silver-light) 0%, var(--silver) 45%, var(--silver-dark) 100%);
  }
  .card--back {
    top: 470px;
    background: var(--paper);
  }
  .brand {
    display: flex;
    align-items: center;
    gap: 14px;
    color: var(--paper);
    font-weight: 700;
    font-size: 64px;
    letter-spacing: 2px;
    line-height: 1;
  }
  .brand__mark {
    width: 44px;
    height: 44px;
    background: var(--paper);
  }
  .card--front .brand {
    position: absolute;
    left: 50%;
    top: 118px;
    transform: translateX(-50%);
  }
  .card--front .website {
    position: absolute;
    left: 0; right: 0;
    top: 262px;
    text-align: center;
    color: var(--paper);
    font-size: 15px;
    letter-spacing: 7px;
  }
  .card--back .brand {
    position: absolute;
    left: 70px;
    top: 120px;
    color: var(--silver-mid);
  }
  .card--back .brand__mark { background: var(--silver-mid); }
  .name-tag {
    position: absolute;
    right: 0;
    top: 92px;
    width: 260px;
    height: 90px;
  }
  .name-tag svg { display: block; }
  .name-tag__label {
    position: absolute;
    right: 26px;
    top: 33px;
    font-weight: 700;
    font-size: 17px;
    line-height: 24px;
    color: var(--ink-dark);
    text-transform: uppercase;
  }
  .contact {
    position: absolute;
    left: 70px;
    top: 250px;
    color: var(--ink);
    font-size: 15px;
    line-height: 21px;
    list-style: none;
  }
  .contact li { display: flex; align-items: center; gap: 9px; }
  .contact svg { width: 13px; height: 13px; fill: var(--ink); flex: none; }
</style>
</head>
<body>
  <section class="card card--front">
    <div class="brand"><span class="brand__mark"></span>KVTL</div>
    <p class="website">www.agentur-kvtl.de</p>
  </section>

  <section class="card card--back">
    <div class="brand"><span class="brand__mark"></span>KVTL</div>

    <div class="name-tag">
      <svg width="260" height="90" viewBox="0 0 260 90">
        <polygon points="60,20 260,20 260,70 60,70 60,86 8,45 60,4" fill="var(--tag)"/>
      </svg>
      <span class="name-tag__label">Lena Vogt</span>
    </div>

    <ul class="contact">
      <li>Kellberger Str. 18</li>
      <li>72486 Brunnstadt</li>
      <li><svg viewBox="0 0 16 16"><path d="M3 1h3l1.5 4-2 1.3a9 9 0 0 0 4.2 4.2L11 8.5l4 1.5v3a2 2 0 0 1-2 2A12 12 0 0 1 1 3a2 2 0 0 1 2-2z"/></svg>07146-839214-0</li>
      <li><svg viewBox="0 0 16 16"><path d="M1 3h14v10H1z M1 3l7 6 7-6" stroke="#fff" stroke-width="1.2"/></svg>Name@agentur-kvtl.de</li>
      <li><svg viewBox="0 0 16 16"><circle cx="8" cy="8" r="7"/><path d="M1 8h14M8 1c-3 3-3 11 0 14M8 1c3 3 3 11 0 14" stroke="#fff" stroke-width="1" fill="none"/></svg>www.agentur-kvtl.de</li>
    </ul>
  </section>
</body>
</html>
```